Luxury Business Card Design for High-End Window Treatments

Gilded Slatworks
Custom Plantation Shutters & Architectural Shading Systems

⸻

BACK

Daniel Trevick
Owner

Custom Interior & Exterior Window Treatments

919-555-0148
gildedslatworks.com

I have included a picture that I’m hoping we can use on the back, but I’m also wondering if you can get rid of the ladder? Should we get rid of shutters , shades and blinds underneath Gilded Slatworks?

Target Market(s)

High-end residential homeowners, custom home builders, architects, interior designers, and luxury renovation clients seeking premium plantation shutters and motorized architectural shading systems.

Industry/Entity Type

Custom Window treatments

Contact Information for Business Card

Front Gilded Slatworks Custom Plantation Shutters Motorized Architectural Shading Systems BACK Daniel Trevick Owner 919-555-0148 GildedSlatworks.com Custom Interior & Exterior Window Treatments By Appointment

Requirements
Nice to have
• Not 100% sure on nice to halves or the color but you can definitely check out my website to get a better understanding of what I’m trying to do

```html
<!DOCTYPE html>
<html lang="en">
<head>
<meta charset="utf-8">
<title>Gilded Slatworks – Business Card</title>
<link rel="stylesheet" href="https://fonts.googleapis.com/css2?family=Lora:wght@400;600;700&family=Montserrat:wght@400&display=swap">
<style>
  :root {
    --backdrop: #3a3a3c;
    --gold-light: #dcc073;
    --gold-mid: #a8854a;
    --gold-deep: #7a5631;
    --ink: #141414;
    --card-dark: #262626;
    --white: #f4f1ea;
  }
  * { box-sizing: border-box; margin: 0; padding: 0; }
  html, body { width: 1200px; height: 758px; overflow: hidden; }
  body {
    background: var(--backdrop);
    display: flex;
    align-items: center;
    justify-content: center;
    gap: 40px;
  }
  .card {
    position: relative;
    width: 560px;
    height: 320px;
    border-radius: 22px;
    overflow: hidden;
  }

  /* Front */
  .card-front {
    background: linear-gradient(100deg, var(--gold-light) 0%, var(--gold-mid) 45%, var(--gold-deep) 100%);
    display: flex;
    flex-direction: column;
    align-items: center;
    justify-content: center;
    color: var(--ink);
  }
  .front-name {
    font-family: 'Lora', serif;
    font-weight: 400;
    font-size: 56px;
    line-height: 1.05;
    text-align: center;
  }
  .front-services {
    margin-top: 22px;
    font-family: 'Lora', serif;
    font-weight: 700;
    font-size: 26px;
    word-spacing: 22px;
  }

  /* Back */
  .card-back { background: var(--card-dark); }
  .back-art { position: absolute; inset: 0; }
  .back-name {
    position: absolute;
    left: 36px; top: 26px;
    font-family: 'Lora', serif;
    font-weight: 400;
    font-size: 32px;
    line-height: 1.0;
    color: var(--gold-light);
  }
  .holder {
    position: absolute;
    left: 40px; top: 130px;
    color: var(--ink);
  }
  .holder-name {
    font-family: 'Lora', serif;
    font-weight: 600;
    font-size: 25px;
    letter-spacing: 0.5px;
    line-height: 1;
  }
  .holder-role {
    font-family: 'Montserrat', sans-serif;
    font-size: 13px;
    margin-top: 4px;
  }
  .specialty {
    position: absolute;
    left: 40px; top: 196px;
    font-family: 'Lora', serif;
    font-weight: 700;
    font-size: 16px;
    line-height: 1.35;
    color: var(--gold-light);
  }
  .contact {
    position: absolute;
    left: 40px; top: 252px;
    list-style: none;
    font-family: 'Lora', serif;
    font-size: 16px;
    color: var(--white);
  }
  .contact li { display: flex; align-items: center; gap: 9px; height: 26px; }
  .contact-icon { width: 18px; height: 18px; flex: none; }
</style>
</head>
<body>

  <section class="card card-front" aria-label="Card front">
    <h1 class="front-name">Gilded<br>Slatworks</h1>
    <p class="front-services">Shutters Shades Blinds</p>
  </section>

  <section class="card card-back" aria-label="Card back">
    <svg class="back-art" width="560" height="320" viewBox="0 0 560 320" aria-hidden="false">
      <defs>
        <linearGradient id="bandGold" x1="0" x2="1" y1="0" y2="0">
          <stop offset="0" stop-color="#9a7740"/>
          <stop offset="0.5" stop-color="#d8bc6c"/>
          <stop offset="1" stop-color="#dcc073"/>
        </linearGradient>
        <linearGradient id="photoTones" x1="0" x2="0" y1="0" y2="1">
          <stop offset="0" stop-color="#6fa3d8"/>
          <stop offset="0.35" stop-color="#a7c2da"/>
          <stop offset="0.6" stop-color="#3d4656"/>
          <stop offset="1" stop-color="#4d5a3a"/>
        </linearGradient>
      </defs>
      <rect class="name-band" x="0" y="126" width="420" height="56" fill="url(#bandGold)"/>
      <circle class="photo-ring" cx="480" cy="110" r="208" fill="#d8bc6c"/>
      <circle class="photo-gap" cx="480" cy="110" r="201" fill="var(--card-dark)"/>
      <circle class="photo-area" cx="480" cy="110" r="195" fill="url(#photoTones)"
              role="img" aria-label="Photo of a home's covered porch with exterior screen shades, white columns and garden chairs"/>
    </svg>

    <p class="back-name">Gilded<br>Slatworks</p>

    <div class="holder">
      <h2 class="holder-name">DANIEL TREVICK</h2>
      <p class="holder-role">Owner</p>
    </div>

    <p class="specialty">Custom Interior &amp; Exterior<br>Window Treatments</p>

    <ul class="contact">
      <li>
        <svg class="contact-icon" viewBox="0 0 18 18" aria-hidden="true">
          <circle cx="9" cy="9" r="9" fill="#d8bc6c"/>
          <path d="M5.5 5 h2 l1 2.3 -1.2 1 a6 6 0 0 0 2.4 2.4 l1-1.2 2.3 1 v2 a1 1 0 0 1 -1 1 A7.5 7.5 0 0 1 4.5 6 a1 1 0 0 1 1-1z" fill="#262626"/>
        </svg>
        919-555-0148
      </li>
      <li>
        <svg class="contact-icon" viewBox="0 0 18 18" aria-hidden="true">
          <circle cx="9" cy="9" r="9" fill="#d8bc6c"/>
          <circle cx="9" cy="9" r="5" fill="none" stroke="#262626" stroke-width="1.2"/>
          <ellipse cx="9" cy="9" rx="2.2" ry="5" fill="none" stroke="#262626" stroke-width="1"/>
          <line x1="4" y1="9" x2="14" y2="9" stroke="#262626" stroke-width="1"/>
        </svg>
        gildedslatworks.com
      </li>
    </ul>
  </section>

</body>
</html>
```